Recruitment Site Design

We need a design for the login page, about page, and inner pages of a recruitment site for an oil and gas company. Design should be modern, sleek, professional and colors can be blue, green, white, orange or any other recommended colors.

Please also take into consideration that once the users login, they will need to access a form to fill in their information.

** UPDATE: Kindly provide a design for the inner information page consistent with the outer design. Attached is a picture of the basic structure. ***
Updates

Please provide a design for inner pages as shown in the design brief consistent with the registration page provided. 

Reason: We're extending it to get more inside pages.

Target Market(s)

Professionals looking for a career in the oil and gas industry in the Middle East.

Industry/Entity Type

Oil And Gas

Requirements
Must have
• Sleek design

```html
<!DOCTYPE html>
<html lang="en">
<head>
<meta charset="utf-8">
<title>Rigline – Jobs in Oil &amp; Gas</title>
<link href="https://fonts.googleapis.com/css2?family=Open+Sans:wght@400;600;700&display=swap" rel="stylesheet">
<style>
:root{
  --sand-top:#ead3ad;
  --sand-bottom:#dcb27a;
  --panel:#e8d3ae;
  --field:#f2e6d2;
  --orange:#f47a12;
  --orange-light:#ff9a2e;
  --red:#e8261a;
  --ink:#333;
  --ink-soft:#444;
  --link:#e2541b;
  --label:#e0561c;
  --white:#fff;
  --frame:#ececec;
}
*{box-sizing:border-box;margin:0;padding:0}
html,body{width:987px;height:1200px;overflow:hidden}
body{position:relative;background:var(--white);font-family:"Open Sans",Arial,sans-serif;color:var(--ink)}
.top-band{position:absolute;left:0;top:0;width:987px;height:370px;background:linear-gradient(#e9d2ad,#ddb47b)}
.abs{position:absolute}

.site-search{left:646px;top:38px;width:210px;height:19px;background:var(--white);font-size:8px;color:#aaa;font-style:italic;padding:4px 6px}

.frame{left:128px;top:64px;width:730px;height:378px;background:var(--frame);border-radius:6px;box-shadow:0 6px 10px rgba(0,0,0,.12)}
.logo-cut{left:128px;top:60px;width:130px;height:52px;background:linear-gradient(#e6cca2,#e2c393);display:flex;align-items:center;justify-content:center;z-index:2}
.logo{font-size:33px;font-weight:700;color:var(--white);letter-spacing:-.5px;line-height:1;white-space:nowrap}
.nav{left:258px;top:64px;width:600px;height:48px;display:flex;justify-content:space-around;align-items:center;font-size:13px;color:#444;background:var(--frame);border-radius:0 6px 0 0}

.hero{left:142px;top:124px;width:703px;height:241px;background:radial-gradient(ellipse at 62% 55%,#fbc63e 0%,#e98a19 30%,#9a4a0e 65%,#3a1b07 100%)}
.hero-title{left:174px;top:191px;font-size:26px;font-weight:700;color:var(--white);line-height:34px;letter-spacing:-.3px}

.login{left:554px;top:195px;width:276px;height:88px;background:rgba(238,238,238,.95);border-radius:6px;font-size:8px;color:#333}
.login h3{position:absolute;left:22px;top:10px;font-size:10px;font-weight:600}
.login .lbl{position:absolute;left:23px}
.login .inp{position:absolute;left:70px;width:129px;height:15px;background:var(--white);border-top:1px solid #bbb}
.login .remember{position:absolute;left:22px;top:73px;display:flex;align-items:center;gap:4px;font-weight:600}
.login .box{width:7px;height:7px;border:1px solid #999;background:var(--white)}
.login .forgot{position:absolute;left:117px;top:73px;color:#7a3d10;text-decoration:underline;font-weight:600}
.btn{display:flex;align-items:center;justify-content:center;background:linear-gradient(var(--orange-light),var(--orange));color:var(--white);border-radius:12px;font-weight:600;box-shadow:0 2px 3px rgba(0,0,0,.2)}
.login .btn{position:absolute;left:205px;top:39px;width:60px;height:15px;font-size:7px}

.signup{left:143px;top:377px;width:704px;height:52px;background:linear-gradient(var(--orange-light) 0%,#f5501a 55%,var(--red) 100%);display:flex;align-items:center}
.signup .big{margin-left:44px;font-size:20px;font-weight:700;color:var(--white);text-decoration:underline}
.signup .small{margin-left:14px;font-size:13px;color:var(--white)}
.signup .email{position:absolute;left:394px;top:15px;width:267px;height:27px;border-radius:14px;background:#4a1208;color:var(--white);font-size:10px;padding:6px 16px}

.filter{font-size:10px}
.filter .lbl{position:absolute;color:var(--label);font-size:11px}
.filter .fld{position:absolute;height:15px;border:1px solid #bbb;font-size:8px;padding:2px 6px;color:#444;background:var(--white)}
.filter .fld.dd::after{content:"";position:absolute;right:8px;top:4px;border:4px solid transparent;border-top:6px solid #666;border-bottom:0}
.filter .go{position:absolute;left:731px;top:474px;width:101px;height:26px;font-size:12px;border-radius:14px}

.content{left:128px;top:528px;width:730px;height:586px;background:var(--panel);box-shadow:14px 14px 14px rgba(0,0,0,.12)}
.h2{position:absolute;font-size:13px;font-weight:700;color:#333}
.cat{position:absolute;list-style:none;font-size:8.5px;color:#444}
.cat li{display:flex;align-items:center;height:18.3px}
.cat.right li{height:19.8px}
.cat svg{margin-left:-24px;margin-right:16px}
.view-more{left:406px;top:776px;font-size:8.5px;color:var(--link);text-decoration:underline}

.qs{position:absolute;left:574px;width:275px;background:var(--field);font-size:10px;color:#333;padding-left:14px;display:flex;align-items:center}
.qs small{font-size:8px}
.upload{align-items:flex-start;padding-top:8px}
.btn.sm{position:absolute;height:21px;font-size:10px}

.about-img{left:166px;top:857px;width:335px;height:97px;background:linear-gradient(#1f1208 0%,#a04a10 45%,#f4a630 80%,#fff0c8 100%)}
.about-text{left:166px;top:966px;width:335px;font-size:8.3px;line-height:12.8px;color:#222}

.job{position:absolute;left:576px;width:273px;font-size:8px;line-height:12px;color:#222}
.job h4{font-size:9.5px;font-weight:700;margin-bottom:1px;color:#222}
.job a{display:block;text-align:right;color:var(--link);text-decoration:underline;font-size:8px;margin-top:7px}

.social{left:731px;top:1130px;display:flex;gap:4px}
.social span{width:28px;height:28px;border-radius:50%;background:var(--orange);display:block}
.copy{left:128px;top:1175px;font-size:8px;color:#333}
.foot-nav{left:540px;top:1174px;width:318px;display:flex;justify-content:space-between;font-size:9px;color:#333}
</style>
</head>
<body>
<div class="top-band"></div>
<div class="abs site-search">Search</div>

<div class="abs frame"></div>
<nav class="abs nav"><span>About us</span><span>Jobs</span><span>Blog</span><span>Find Now</span><span>Location</span><span>Contact</span></nav>
<div class="abs logo-cut"><span class="logo">Rigline</span></div>

<div class="abs hero" role="img" aria-label="Photo of a drilling rig silhouetted against an orange sunset"></div>
<div class="abs hero-title">JOBS IN<br>OIL &amp; GAS INDUSTRY</div>

<form class="abs login">
  <h3>LOGIN</h3>
  <span class="lbl" style="top:34px">Username</span><span class="inp" style="top:33px"></span>
  <span class="lbl" style="top:58px">Password</span><span class="inp" style="top:57px"></span>
  <span class="btn">Sign In</span>
  <span class="remember"><span class="box"></span>keep reminded</span>
  <span class="forgot">Forgot your Password ?</span>
</form>

<div class="abs signup">
  <span class="big">SIGN UP</span><span class="small">for free &amp; get your jobs to your mailbox</span>
  <span class="email">Enter your E-mail address</span>
</div>

<div class="filter">
  <span class="lbl" style="left:154px;top:469px">Keywords</span>
  <span class="fld" style="left:215px;top:470px;width:197px">Job Title / Job Ref Number</span>
  <span class="lbl" style="left:157px;top:495px">Locations</span>
  <span class="fld dd" style="left:215px;top:494px;width:197px">All Locations</span>
  <span class="lbl" style="left:462px;top:467px">Sector</span>
  <span class="fld dd" style="left:513px;top:468px;width:197px">All Sectors</span>
  <span class="lbl" style="left:451px;top:493px">Job Type</span>
  <span class="fld dd" style="left:513px;top:493px;width:197px">All Job Types</span>
  <span class="btn go">Search Now</span>
</div>

<section class="abs content"></section>

<h2 class="h2" style="left:168px;top:547px">VIEW JOBS IN CATEGORY</h2>
<ul class="cat" style="left:208px;top:573px">
  <li><svg width="8" height="6"><path d="M0 3h6M4 1l2 2-2 2" stroke="#fff" fill="none"/></svg>Administration</li>
  <li><svg width="8" height="6"><path d="M0 3h6M4 1l2 2-2 2" stroke="#fff" fill="none"/></svg>Commercial/Financial/Legal</li>
  <li><svg width="8" height="6"><path d="M0 3h6M4 1l2 2-2 2" stroke="#fff" fill="none"/></svg>Design</li>
  <li><svg width="8" height="6"><path d="M0 3h6M4 1l2 2-2 2" stroke="#fff" fill="none"/></svg>Drilling</li>
  <li><svg width="8" height="6"><path d="M0 3h6M4 1l2 2-2 2" stroke="#fff" fill="none"/></svg>Engineering</li>
  <li><svg width="8" height="6"><path d="M0 3h6M4 1l2 2-2 2" stroke="#fff" fill="none"/></svg>Environment</li>
  <li><svg width="8" height="6"><path d="M0 3h6M4 1l2 2-2 2" stroke="#fff" fill="none"/></svg>Geoscience</li>
  <li><svg width="8" height="6"><path d="M0 3h6M4 1l2 2-2 2" stroke="#fff" fill="none"/></svg>Health &amp; Safety</li>
  <li><svg width="8" height="6"><path d="M0 3h6M4 1l2 2-2 2" stroke="#fff" fill="none"/></svg>HR/Personnel/Training</li>
  <li><svg width="8" height="6"><path d="M0 3h6M4 1l2 2-2 2" stroke="#fff" fill="none"/></svg>Technician</li>
  <li><svg width="8" height="6"><path d="M0 3h6M4 1l2 2-2 2" stroke="#fff" fill="none"/></svg>Terminal/Refinery/Distribution</li>
  <li><svg width="8" height="6"><path d="M0 3h6M4 1l2 2-2 2" stroke="#fff" fill="none"/></svg>Trades</li>
</ul>
<ul class="cat right" style="left:382px;top:573px">
  <li><svg width="8" height="6"><path d="M0 3h6M4 1l2 2-2 2" stroke="#fff" fill="none"/></svg>IT/Communications</li>
  <li><svg width="8" height="6"><path d="M0 3h6M4 1l2 2-2 2" stroke="#fff" fill="none"/></svg>Logistics/Procurement</li>
  <li><svg width="8" height="6"><path d="M0 3h6M4 1l2 2-2 2" stroke="#fff" fill="none"/></svg>Management</li>
  <li><svg width="8" height="6"><path d="M0 3h6M4 1l2 2-2 2" stroke="#fff" fill="none"/></svg>Marine/Diving/ROV</li>
  <li><svg width="8" height="6"><path d="M0 3h6M4 1l2 2-2 2" stroke="#fff" fill="none"/></svg>Oil Sands</li>
  <li><svg width="8" height="6"><path d="M0 3h6M4 1l2 2-2 2" stroke="#fff" fill="none"/></svg>Operations (other)</li>
  <li><svg width="8" height="6"><path d="M0 3h6M4 1l2 2-2 2" stroke="#fff" fill="none"/></svg>Quality/Inspection</li>
  <li><svg width="8" height="6"><path d="M0 3h6M4 1l2 2-2 2" stroke="#fff" fill="none"/></svg>Sales/Marketing</li>
  <li><svg width="8" height="6"><path d="M0 3h6M4 1l2 2-2 2" stroke="#fff" fill="none"/></svg>Science (other)</li>
</ul>
<a class="abs view-more">View more</a>

<h2 class="h2" style="left:571px;top:549px">QUICK SEARCH</h2>
<div class="qs" style="top:574px;height:32px">Name</div>
<div class="qs" style="top:616px;height:28px">E-mail Address</div>
<div class="qs upload" style="top:654px;height:100px">Upload as a&nbsp;<small>( Word Document &nbsp;or pdf files)</small></div>
<span class="btn sm" style="left:627px;top:720px;width:95px">Choose a File</span>
<span class="btn sm" style="left:732px;top:720px;width:79px">Edit your CV</span>
<span class="btn sm" style="left:672px;top:763px;width:79px">Send</span>

<h2 class="h2" style="left:168px;top:827px">ABOUT US</h2>
<div class="abs about-img" role="img" aria-label="Illustration of business people silhouetted against a warm glow"></div>
<p class="abs about-text">Lorem Ipsum is simply dummy text of the printing and typesetting industry. Lorem Ipsum has been the industry's standard dummy text ever since the 1500s, when an unknown printer took a galley of type and scrambled it to make a type specimen book. It has survived not only five centuries, but also the leap into electronic typesetting, remaining essentially unchanged.</p>

<h2 class="h2" style="left:576px;top:827px">LATEST JOBS</h2>
<div class="job" style="top:855px">
  <h4>CONSTRUCTION MANAGER-US NATIONAL'S ONLY</h4>
  Contract / Interim United States<br>On Application Please<br>Construction manager for a Gas processing facility in London
  <a>VIEW / APPLY</a>
</div>
<div class="job" style="top:940px">
  <h4>MECHANICAL &amp; PIPING ENGINEER</h4>
  Contract / InterimItaly<br>€20 - €60 per hour + benefits<br>Main Job Function: To review and approve the specification,
  <a style="margin-top:14px">VIEW / APPLY</a>
</div>
<div class="job" style="top:1029px">
  <h4>CONSTRUCTION MANAGER-US NATIONAL'S ONLY</h4>
  Contract / Interim United States<br>On Application Please<br>Construction manager for a Gas processing facility in London
  <a>VIEW / APPLY</a>
</div>

<div class="abs social" aria-label="Social links"><span></span><span></span><span></span><span></span></div>
<div class="abs copy">Copyright © @ Rigline 2012. All Rights Reserved.</div>
<nav class="abs foot-nav"><span>Home</span><span>About us</span><span>Contact</span><span>Terms &amp; Conditions</span><span>Privacy Policy</span></nav>
</body>
</html>
```